VocaTerrana Community/ Talent Gallery

VocaTerrana is developing a collaborative career course, with coaching and community exchange. Goal is to offer a platform where talented candidates can show their expertise and find projects, partners, and develop their online portfolios!

Here is a good example of the type of thing we hope to create with focus on sustainability focused talent to task matching
http://www.brambleforth.com/global-themes/employment-and-growth/connecting-talent-with-opportunity-in-the-digital-age

We hope to have a "grid style" gallery where it is easy to search by talent types and focus areas within the scope of "Sustainability" issues...Food/Water/Energy, Public Health, Technology, Sustainable Cities, Infrastructure, Education, Policy, Emerging Economies, Ecosystems, Social Innovation, inclusive Security, Equity Issues. For each topic/ header we hope to have candidates post their completed portfolios to exhibit resumes, biography, a case study... they may actually prepare these on other sites, but can link in OR alternately that they can easily create here, similar to "pinqo.io" ....

Hope to include a blog space titled "Rising over the Rift", where people can mix it up across these topic issues as they are interdependent and often require partners across discipline areas! If possible another area where jobs related to these issues may be posted as project or job opportunities by potential employers.

If there is a way to create a feed from various job sites that already exist...like Jobora...or http://www.greenledgerworks.com/ that would be super great. Again...sort of a portal connection to bridge the gap ....instead of candidates having to search all the time, we are hoping they can advertise their talent and employers may search here for these well presented portfolios!

Target Market(s)

Educators, Students, Career Transitioners, Employers, Professional Associations, Talent Recruiters with focus on Sustainability related Talent to Task matching!

Industry/Entity Type

Sustainability

Number of Pages Required

4 page

Font styles to use
Sans Serif

Colors
3176b5
32b8a4
add136

Requirements
Must have
• Not sure about the coded/ uncoded option here....
• Must have - grid style area where Sustainability Professionals with varied focus areas can exhibit their talent portfolios
• appear as a Talent Gallery that starts with photos & obvious organization...other tabs to be in a menu.
• ability to search both talent and task opportunity areas to help coaches or community members make matches....some topic focused category or tag words to help make them searchable...???
• consistent professional styling to existing website and new artflock postcard shared in brief/ images area
• Interactive blog space where articles, issues may be posted, discussed
• Bulletin board or feed for project opportunities to be posted where candidates may locate them and/or employers may express specific "call" for talent..These may be Short term Internships, Projects, Consulting Team Opportunity, or Jobs/ part time to full time....
Nice to have
• A calendar area where we can post networking opportunities, issues presentations where potential partners can meet the next generation leaders, attend a forum or webinar presentation.
Should not have
• Too much text on front page...Should be clean design,

```html
<!DOCTYPE html>
<html lang="en">
<head>
<meta charset="utf-8">
<title>VocaTerrana – Talent Gallery</title>
<link href="https://fonts.googleapis.com/css2?family=Lato:wght@300;400;700;900&display=swap" rel="stylesheet">
<style>
:root{
  --blue:#3176b5;
  --blue-bright:#1f80cf;
  --teal:#32b8a4;
  --teal-deep:#0f7f72;
  --green:#add136;
  --green-nav:#8cc63f;
  --ink:#1b1b1b;
  --text:#444;
  --grey-bg:#eeeeee;
  --footer:#0d1b2a;
  --footer-line:#24364a;
  --white:#fff;
}
*{box-sizing:border-box;margin:0;padding:0}
html,body{width:1200px;height:4027px;overflow:hidden}
body{font-family:'Lato',Arial,sans-serif;color:var(--text);background:var(--white);position:relative}
a{color:inherit;text-decoration:none}
.section{position:absolute;left:0;width:1200px}

/* header */
.site-header{top:0;height:86px}
.brand{position:absolute;left:100px;top:16px;display:flex;align-items:center;gap:14px}
.brand-dot{width:54px;height:54px;border-radius:50%;background:var(--teal)}
.brand-name{font-size:40px;font-weight:400;color:var(--ink)}
.header-tools{position:absolute;right:100px;top:30px;display:flex;align-items:center;gap:18px;font-size:17px;color:var(--ink)}
.phone{display:flex;align-items:center;gap:8px}
.login-btn{background:var(--blue);color:#fff;font-size:12px;font-weight:700;padding:5px 12px;border-radius:12px}

.main-nav{top:86px;height:35px;background:var(--green-nav)}
.main-nav ul{list-style:none;display:flex;justify-content:space-between;width:1000px;margin-left:100px;height:35px}
.main-nav li{font-size:14px;color:#fff;padding:0 17px;line-height:35px;text-transform:uppercase}
.main-nav li.active{background:var(--teal-deep);font-weight:700}

/* hero */
.hero{top:121px;height:470px;background:linear-gradient(90deg,#8b6148 0%,#c49a7c 18%,#5f8fbf 40%,#3f7ab2 55%,#c49a7c 80%,#8b6148 100%)}
.hero-arrow{position:absolute;top:190px}
.hero-arrow.left{left:30px}.hero-arrow.right{right:30px}
.hero-caption{position:absolute;left:0;bottom:0;width:1200px;height:81px;background:rgba(30,30,30,.72);padding:12px 0 0 120px;color:#fff}
.hero-caption h1{font-size:31px;font-weight:700}
.hero-caption p{font-size:19px;font-weight:700;margin-top:2px}
.pill-btn{display:inline-flex;align-items:center;gap:10px;background:var(--teal);color:#fff;font-size:15px;font-weight:700;padding:4px 22px 4px 4px;border-radius:30px}
.pill-btn .dot{width:40px;height:40px;border-radius:50%;background:#fff}
.hero-caption .pill-btn{position:absolute;left:866px;top:16px}

/* welcome */
.welcome{top:591px;height:429px}
.welcome-copy{position:absolute;left:100px;top:36px;width:560px}
.welcome-copy h2{font-size:36px;font-weight:900;color:var(--ink)}
.welcome-copy h2 span{font-weight:400}
.welcome-copy p{font-size:15px;line-height:21px;margin-top:14px;color:#333}
.welcome-copy ul{margin:12px 0 0 18px;font-size:15px;line-height:27px;color:#333}
.welcome-copy .pill-btn{margin-top:22px;font-size:14px;padding-right:18px}
.welcome-copy .pill-btn .dot{width:34px;height:34px}
.phase-panel{position:absolute;right:0;top:0;width:475px;height:429px}
.phase-panel svg.bg{position:absolute;left:0;top:0}
.phase-content{position:absolute;left:50px;top:38px;color:#fff}
.phase-content h3{font-size:31px;font-weight:700;line-height:34px}
.phase-content h3 span{display:block;font-weight:400}
.phase-list{list-style:none;margin-top:20px}
.phase-list li{display:flex;align-items:center;gap:18px;height:67px}
.phase-icon{width:52px;height:52px;border-radius:50%;background:#fff;display:flex;align-items:center;justify-content:center;flex:none}
.phase-list strong{display:block;font-size:15px;letter-spacing:3px;font-weight:700}
.phase-list small{display:block;font-size:11px;color:var(--green);max-width:330px}

/* gallery */
.gallery{top:1020px;height:881px;background:var(--grey-bg)}
.section-title{text-align:center;font-size:34px;color:var(--ink);font-weight:400}
.section-title b{font-weight:900}
.gallery .section-title{margin-top:42px}
.tile-grid{position:absolute;left:99px;top:140px;width:1002px;display:grid;grid-template-columns:repeat(6,1fr);grid-auto-rows:167px;gap:11px 18px}
.tile{position:relative;overflow:hidden}
.tile.wide{grid-column:span 2}
.tile span{position:absolute;left:0;right:0;bottom:10px;text-align:center;color:#fff;font-weight:700;font-size:18px;text-shadow:0 1px 3px rgba(0,0,0,.8)}
.gallery-arrow{position:absolute;top:390px}
.gallery-arrow.left{left:30px}.gallery-arrow.right{right:30px}

/* blog */
.blog{top:1901px;height:422px}
.blog .section-title{margin-top:40px;font-size:30px}
.card-row{position:absolute;left:99px;top:130px;width:1002px;display:flex;justify-content:space-between}
.card{width:317px}
.card-img{height:153px;position:relative}
.date-badge{position:absolute;left:6px;top:0;width:44px;height:44px;background:var(--teal-deep);color:#fff;text-align:center;font-weight:900;font-size:17px;line-height:19px;padding-top:4px}
.date-badge small{display:block;font-size:10px;font-weight:700}
.card h4{font-size:14px;color:var(--ink);margin-top:16px;font-weight:700}
.card p{font-size:12px;line-height:15px;color:#555;margin-top:6px}
.read-more{display:inline-block;font-size:12px;color:var(--teal-deep);font-weight:700;margin-top:10px}
.blog-arrow{position:absolute;top:198px}
.blog-arrow.left{left:30px}.blog-arrow.right{right:30px}

/* call for talent */
.call{top:2323px;height:287px;background:var(--blue-bright);color:#fff;text-align:center}
.call h2{font-size:30px;font-weight:900;margin-top:40px}
.call h2 span{font-weight:400}
.call p{font-size:15px;line-height:22px;width:990px;margin:30px auto 0}
.audience{display:flex;justify-content:center;gap:54px;margin-top:36px;font-size:16px;font-weight:700}
.audience li{list-style:none;display:flex;align-items:center;gap:10px}

/* video */
.video{top:2610px;height:456px;background:linear-gradient(180deg,#2b2a30 0%,#4b4038 45%,#6e5e4e 75%,#3b332c 100%)}
.video .section-title{color:#fff;margin-top:30px;font-size:34px}
.play{position:absolute;left:574px;top:245px}

/* news */
.news{top:3066px;height:425px}
.news h2{position:absolute;left:99px;top:34px;font-size:34px;color:var(--ink);font-weight:900}
.news h2 span{font-weight:400}
.news-grid{position:absolute;left:99px;top:108px;width:720px;display:grid;grid-template-columns:1fr 1fr;gap:45px 26px}
.news-item{display:flex;gap:12px}
.news-img{width:185px;height:118px;position:relative;flex:none}
.news-date{position:absolute;right:0;top:0;width:36px;height:118px;background:var(--teal-deep);color:#fff;text-align:center;font-weight:900;font-size:17px;padding-top:4px;line-height:18px}
.news-date small{display:block;font-size:10px;font-weight:700}
.news-item h5{font-size:11px;color:var(--ink);font-weight:700}
.news-item p{font-size:11px;line-height:14px;color:#555;margin-top:6px}
.news-item .read-more{font-size:11px;margin-top:8px}
.calendar{position:absolute;left:854px;top:102px;width:252px}
.calendar h5{font-size:14px;color:var(--ink);font-weight:900;text-align:center}
.cal-box{border:1px solid #ddd;margin-top:8px;padding:6px 8px 8px;border-radius:4px}
.cal-month{display:block;width:120px;margin:0 auto;background:var(--teal);color:#fff;font-size:11px;font-weight:700;text-align:center;padding:3px 0;border-radius:2px}
.cal-box table{width:100%;border-collapse:collapse;margin-top:5px;font-size:11px;text-align:center;color:#333}
.cal-box th{font-size:8px;color:#666;font-weight:700;padding:2px 0}
.cal-box td{padding:3px 0}
.join-btn{display:flex;align-items:center;justify-content:center;gap:10px;margin:12px auto 0;width:200px;height:40px;background:var(--blue);color:#fff;border-radius:22px;font-size:22px;font-weight:900}

/* footer */
.site-footer{top:3491px;height:536px;background:var(--footer);color:#fff}
.footer-nav{list-style:none;display:flex;justify-content:space-between;width:1000px;margin:42px 0 0 100px;font-size:15px;text-transform:uppercase;padding-bottom:20px;border-bottom:1px solid var(--footer-line)}
.contact{position:absolute;left:134px;top:140px;width:360px}
.footer-heading{font-size:19px;font-weight:900}
.contact-row{display:flex;gap:16px;margin-top:20px;font-size:12px;line-height:16px}
.contact-row svg{flex:none;margin-top:2px}
.contact-row b{display:block;font-size:12px}
.follow{margin-top:20px;font-size:12px}
.socials{display:flex;gap:6px;margin-top:8px}
.socials span{width:22px;height:22px;border-radius:3px}
.inquiry{position:absolute;left:717px;top:140px;width:389px}
.form-grid{display:grid;grid-template-columns:1fr 1fr;gap:10px;margin-top:22px}
.field{height:34px;border:1px solid #3c4f63;font-size:12px;padding:0 8px;display:flex;align-items:center;justify-content:space-between;color:#e4e9ee}
.field.full{grid-column:span 2}
.field.message{height:72px;align-items:flex-start;padding-top:8px}
.browse{background:#3c4f63;font-size:11px;padding:3px 10px}
.submit{display:inline-block;background:var(--teal);color:#fff;font-weight:900;font-size:15px;padding:8px 22px;margin-top:10px}
.copyright{position:absolute;left:0;width:1200px;top:500px;text-align:center;font-size:12px;color:#c6ced6}
</style>
</head>
<body>

<header class="section site-header">
  <a class="brand" href="#"><span class="brand-dot"></span><span class="brand-name">VocaTerrana</span></a>
  <div class="header-tools">
    <span class="phone">
      <svg width="22" height="22" viewBox="0 0 24 24"><circle cx="12" cy="12" r="12" fill="#3176b5"/><path d="M8 6l2 3-1.3 1.3a8 8 0 003 3L13 12l3 2-1.2 2.4C10 16 8 14 7.6 9.2z" fill="#fff"/></svg>
      014-552-3970
    </span>
    <span class="login-btn">LOGIN</span>
  </div>
</header>

<nav class="section main-nav">
  <ul>
    <li class="active">Home</li><li>About</li><li>Services</li><li>Blog</li><li>Portfolios</li><li>Partners</li><li>Projects/ Positions</li><li>Perspectives</li><li>Contact</li>
  </ul>
</nav>

<section class="section hero" role="img" aria-label="Photo of hands surrounding a globe of the Earth">
  <svg class="hero-arrow left" width="24" height="90" viewBox="0 0 24 90"><path d="M20 4L4 45l16 41" fill="none" stroke="#fff" stroke-width="3"/></svg>
  <svg class="hero-arrow right" width="24" height="90" viewBox="0 0 24 90"><path d="M4 4l16 41L4 86" fill="none" stroke="#fff" stroke-width="3"/></svg>
  <div class="hero-caption">
    <h1>Career Collaboration For A Sustainable Future</h1>
    <p>Course, Coaching, Community</p>
    <a class="pill-btn" href="#"><span class="dot"></span>Learn More</a>
  </div>
</section>

<section class="section welcome">
  <div class="welcome-copy">
    <h2>Welcome to <span>VocaTerrana</span></h2>
    <p>Lorem ipsum dolor sit amet, consectetur adipiscing elit. Sed vitae magna tellus. Aenean ante nunc, semper nec cursus non, rutrum ac eros. Vestibulum mattis justo ac dui bibendum consequat a ac ipsum.</p>
    <ul>
      <li>Lorem ipsum dolor sit amet, consectetur adipiscing elit</li>
      <li>Lorem ipsum dolor sit amet, consectetu</li>
      <li>Lorem ipsum dolor sit amet, consectetur adipiscing</li>
      <li>Lorem ipsum dolor sit amet, consectetur adip</li>
      <li>Lorem ipsum dolor sit amet, consectetur adipis</li>
    </ul>
    <a class="pill-btn" href="#"><span class="dot"></span>Learn More</a>
  </div>
  <div class="phase-panel">
    <svg class="bg" width="475" height="429" viewBox="0 0 475 429"><path d="M28 0H475V429H0z" fill="#0f7f72"/></svg>
    <div class="phase-content">
      <h3>Four Phase<span>Career Course</span></h3>
      <ul class="phase-list">
        <li><span class="phase-icon"><svg width="30" height="20" viewBox="0 0 30 20"><path d="M1 10C6 2 24 2 29 10 24 18 6 18 1 10z" fill="#0f7f72"/><circle cx="15" cy="10" r="5" fill="#fff"/></svg></span><div><strong>CLARIFY</strong><small>Personal Profile, Vision &amp; Mission</small></div></li>
        <li><span class="phase-icon"><svg width="28" height="24" viewBox="0 0 28 24"><path d="M2 2h18v12H9l-5 4v-4H2z" fill="#0f7f72"/><path d="M22 8h4v10h-2v3l-4-3h-8v-2h10z" fill="#0f7f72"/></svg></span><div><strong>COMMUNICATE</strong><small>Strengths &amp; Strategies for Positive Change</small></div></li>
        <li><span class="phase-icon"><svg width="30" height="22" viewBox="0 0 30 22"><path d="M2 8l8-5 5 3 5-3 8 5-6 9-7 3-7-3z" fill="#0f7f72"/></svg></span><div><strong>COLLABORATE</strong><small>Proactive Projects, Pivoting Performance Results!</small></div></li>
        <li><span class="phase-icon"><svg width="28" height="28" viewBox="0 0 28 28"><circle cx="14" cy="14" r="12" fill="none" stroke="#0f7f72" stroke-width="3"/><path d="M2 14h24M14 2c-6 7-6 17 0 24M14 2c6 7 6 17 0 24" fill="none" stroke="#0f7f72" stroke-width="2"/></svg></span><div><strong>CREATE</strong><small>Creating Change &amp; Innovation for Sustainable Futures!</small></div></li>
      </ul>
    </div>
  </div>
</section>

<section class="section gallery">
  <h2 class="section-title"><b>Talent</b> Gallery</h2>
  <svg class="gallery-arrow left" width="22" height="90" viewBox="0 0 22 90"><path d="M20 2L3 45l17 43" fill="none" stroke="#bbb" stroke-width="3"/></svg>
  <svg class="gallery-arrow right" width="22" height="90" viewBox="0 0 22 90"><path d="M2 2l17 43L2 88" fill="none" stroke="#bbb" stroke-width="3"/></svg>
  <div class="tile-grid">
    <div class="tile wide" role="img" aria-label="Photo of a tree on a green hill under blue sky" style="background:linear-gradient(180deg,#3d8fd6,#7fc0ea 55%,#4f9a2f)"><span>Climate Resilience</span></div>
    <div class="tile" role="img" aria-label="Photo of hands joined together" style="background:linear-gradient(160deg,#9c7a63,#5c6b3c)"><span>Community</span></div>
    <div class="tile" role="img" aria-label="Photo of hands holding a seedling" style="background:linear-gradient(160deg,#c9a38c,#7aa24a)"><span>Ecosystems</span></div>
    <div class="tile wide" role="img" aria-label="Illustration of a magnifying glass over bar charts" style="background:linear-gradient(160deg,#e6e6e6,#9a9a9a)"><span>Economies</span></div>

    <div class="tile" role="img" aria-label="Photo of a graduate with family" style="background:linear-gradient(180deg,#bcd4e8,#8f7a68)"><span>Education</span></div>
    <div class="tile wide" role="img" aria-label="Photo of solar panels under blue sky" style="background:linear-gradient(180deg,#6db1ea,#1f4f9a)"><span>Energy</span></div>
    <div class="tile wide" role="img" aria-label="Illustration of figures watering trees on balanced ground" style="background:linear-gradient(180deg,#f3ead8,#c79a5e)"><span>Equity</span></div>
    <div class="tile" role="img" aria-label="Photo of fresh fruits and vegetables" style="background:linear-gradient(160deg,#c43c1e,#e8a23a)"><span>Food</span></div>

    <div class="tile wide" role="img" aria-label="Aerial photo of a city with a park" style="background:linear-gradient(180deg,#cfe0ee,#6f8f78)"><span>Infrastructure</span></div>
    <div class="tile" role="img" aria-label="Photo of a smiling group of young people" style="background:linear-gradient(160deg,#5b8fd1,#c66f4d)"><span>Public Health</span></div>
    <div class="tile" role="img" aria-label="Photo of a hand holding a green globe" style="background:linear-gradient(160deg,#d9eccb,#3b8f3b)"><span>Policy</span></div>
    <div class="tile wide" role="img" aria-label="Rendering of a green sustainable city" style="background:linear-gradient(180deg,#dfe9e4,#8aa780)"><span>Sustainable Cities</span></div>

    <div class="tile wide" role="img" aria-label="Photo of soldiers walking at sunset" style="background:linear-gradient(180deg,#d8c9a8,#6b5a3f)"><span>Security</span></div>
    <div class="tile wide" role="img" aria-label="Image of a hand touching a digital interface" style="background:linear-gradient(160deg,#1a4f9c,#6fb2e8)"><span>Technology</span></div>
    <div class="tile wide" role="img" aria-label="Photo of a river through forest" style="background:linear-gradient(180deg,#c9dff0,#2f6a4a)"><span>Water</span></div>
  </div>
</section>

<section class="section blog">
  <h2 class="section-title"><b>Rising Over</b> The Rift</h2>
  <svg class="blog-arrow left" width="14" height="26" viewBox="0 0 14 26"><path d="M12 2L2 13l10 11" fill="none" stroke="#333" stroke-width="2.5"/></svg>
  <svg class="blog-arrow right" width="14" height="26" viewBox="0 0 14 26"><path d="M2 2l10 11L2 24" fill="none" stroke="#333" stroke-width="2.5"/></svg>
  <div class="card-row">
    <article class="card">
      <div class="card-img" role="img" aria-label="Illustration of a globe surrounded by nature" style="background:linear-gradient(180deg,#6fb4e4,#2f7a3a)"><span class="date-badge">23<small>JUN</small></span></div>
      <h4>Sed ut perspiciatis unde iste mo</h4>
      <p>Duis autem vel eum iriure dolor in hendrerit ink vulput ate velit esse molestie facilisis.</p>
      <a class="read-more" href="#">Read More »</a>
    </article>
    <article class="card">
      <div class="card-img" role="img" aria-label="Image of a light bulb with wind turbines" style="background:linear-gradient(180deg,#f3f3f3,#b9c4cc)"><span class="date-badge">23<small>JUN</small></span></div>
      <h4>Sed ut perspiciatis unde iste mo</h4>
      <p>Duis autem vel eum iriure dolor in hendrerit ink vulput ate velit esse molestie facilisis.</p>
      <a class="read-more" href="#">Read More »</a>
    </article>
    <article class="card">
      <div class="card-img" role="img" aria-label="Photo of an audience at a conference presentation" style="background:linear-gradient(180deg,#3a4a6a,#8a7060)"><span class="date-badge">23<small>JUN</small></span></div>
      <h4>Sed ut perspiciatis unde iste mo</h4>
      <p>Duis autem vel eum iriure dolor in hendrerit ink vulput ate velit esse molestie facilisis.</p>
      <a class="read-more" href="#">Read More »</a>
    </article>
  </div>
</section>

<section class="section call">
  <h2>Call <span>For Talent</span></h2>
  <p>Lorem ipsum dolor sit amet, consectetur adipiscing elit. Sed vitae magna tellus. Aenean ante nunc, semper nec cursus non, rutrum ac eros. Vestibulum mattis justo ac dui bibendum consequat a ac ipsum.</p>
  <ul class="audience">
    <li><svg width="26" height="22" viewBox="0 0 26 22"><path d="M13 1L1 7h24z M3 9h3v9H3z M9 9h3v9H9z M14 9h3v9h-3z M20 9h3v9h-3z M1 19h24v3H1z" fill="#fff"/></svg>Government</li>
    <li><svg width="26" height="22" viewBox="0 0 26 22"><path d="M2 4h8v18H2z M12 0h12v22H12z" fill="#fff"/></svg>Commercial</li>
    <li><svg width="24" height="24" viewBox="0 0 24 24"><path d="M12 21C3 14 2 10 4 6s7-3 8 1c1-4 6-5 8-1s1 8-8 15z" fill="none" stroke="#fff" stroke-width="2"/></svg>Non-Profit</li>
    <li><svg width="30" height="22" viewBox="0 0 30 22"><path d="M15 1L1 8l14 7 14-7z M6 11v6c5 4 13 4 18 0v-6l-9 5z" fill="#fff"/></svg>Education</li>
    <li><svg width="32" height="24" viewBox="0 0 32 24"><circle cx="7" cy="5" r="4" fill="#fff"/><circle cx="25" cy="5" r="4" fill="#fff"/><path d="M2 22l3-12h4l7 5 7-5h4l3 12h-4l-2-7-8 5-8-5-2 7z" fill="#fff"/></svg>Partnerships</li>
  </ul>
</section>

<section class="section video" role="img" aria-label="Photo of people joining hands in a circle, with hands holding a tablet playing a video">
  <h2 class="section-title"><b>Watch</b> Video</h2>
  <svg class="play" width="52" height="52" viewBox="0 0 52 52"><circle cx="26" cy="26" r="26" fill="#c8102e"/><path d="M21 16l15 10-15 10z" fill="#fff"/></svg>
</section>

<section class="section news">
  <h2>News <span>&amp; Events</span></h2>
  <div class="news-grid">
    <article class="news-item">
      <div class="news-img" role="img" aria-label="Photo of a tree on a green hill" style="background:linear-gradient(180deg,#7cc0ea,#3f8a2f)"><span class="news-date">05<small>Jul</small><small>2016</small></span></div>
      <div><h5>Lorem Ipsum Doloronsecte</h5><p>Sed ut perspiciatis unde omnis iste natus error sit voluptatem accus.</p><a class="read-more" href="#">Read More »</a></div>
    </article>
    <article class="news-item">
      <div class="news-img" role="img" aria-label="Image of a businessman with a digital network" style="background:linear-gradient(180deg,#3e6f9e,#b8cfe0)"><span class="news-date">05<small>Jul</small><small>2016</small></span></div>
      <div><h5>Lorem Ipsum Doloronsecte</h5><p>Sed ut perspiciatis unde omnis iste natus error sit voluptatem accus.</p><a class="read-more" href="#">Read More »</a></div>
    </article>
    <article class="news-item">
      <div class="news-img" role="img" aria-label="Photo of a domed government building" style="background:linear-gradient(180deg,#a8c8e6,#e9e6df)"><span class="news-date">05<small>Jul</small><small>2016</small></span></div>
      <div><h5>Lorem Ipsum Doloronsecte</h5><p>Sed ut perspiciatis unde omnis iste natus error sit voluptatem accus.</p><a class="read-more" href="#">Read More »</a></div>
    </article>
    <article class="news-item">
      <div class="news-img" role="img" aria-label="Photo of many hands stacked together" style="background:linear-gradient(160deg,#c89a7a,#6f4f3a)"><span class="news-date">05<small>Jul</small><small>2016</small></span></div>
      <div><h5>Lorem Ipsum Doloronsecte</h5><p>Sed ut perspiciatis unde omnis iste natus error sit voluptatem accus.</p><a class="read-more" href="#">Read More »</a></div>
    </article>
  </div>
  <aside class="calendar">
    <h5>Calendar &amp; Announcements</h5>
    <div class="cal-box">
      <span class="cal-month">JULY 2016</span>
      <table>
        <tr><th>SUN</th><th>MON</th><th>TUE</th><th>WED</th><th>THU</th><th>FRI</th><th>SAT</th></tr>
        <tr><td>1</td><td>2</td><td>3</td><td>4</td><td>5</td><td>6</td><td>7</td></tr>
        <tr><td>8</td><td>9</td><td>10</td><td>11</td><td>12</td><td>13</td><td>14</td></tr>
        <tr><td>15</td><td>16</td><td>17</td><td>18</td><td>19</td><td>20</td><td>21</td></tr>
        <tr><td>22</td><td>23</td><td>24</td><td>25</td><td>26</td><td>27</td><td>28</td></tr>
        <tr><td>29</td><td>30</td><td>31</td><td></td><td></td><td></td><td></td></tr>
      </table>
    </div>
    <a class="join-btn" href="#"><svg width="26" height="22" viewBox="0 0 26 22"><circle cx="13" cy="5" r="4" fill="#fff"/><circle cx="5" cy="8" r="3" fill="#fff"/><circle cx="21" cy="8" r="3" fill="#fff"/><path d="M7 22v-8c0-3 3-4 6-4s6 1 6 4v8z M0 22v-6c0-2 2-3 4-3l1 9z M26 22v-6c0-2-2-3-4-3l-1 9z" fill="#fff"/></svg>JOIN US</a>
  </aside>
</section>

<footer class="section site-footer">
  <ul class="footer-nav">
    <li>Home</li><li>About</li><li>Services</li><li>Blog</li><li>Portfolios</li><li>Partners</li><li>Projects/ Positions</li><li>Perspectives</li><li>Contact</li>
  </ul>
  <div class="contact">
    <h3 class="footer-heading">CONTACT DETAILS</h3>
    <div class="contact-row">
      <svg width="16" height="22" viewBox="0 0 16 22"><path d="M8 0a8 8 0 018 8c0 6-8 14-8 14S0 14 0 8a8 8 0 018-8z" fill="#fff"/><circle cx="8" cy="8" r="3" fill="#0d1b2a"/></svg>
      <div><b>VocaTerrana</b>48, Fernhollow Lane, Birch Row,<br>Near Quill Park, Lark Vale, CA - 904172</div>
    </div>
    <div class="contact-row">
      <svg width="18" height="14" viewBox="0 0 18 14"><rect width="18" height="14" rx="2" fill="#fff"/><path d="M1 1l8 7 8-7" fill="none" stroke="#0d1b2a" stroke-width="1.5"/></svg>
      <div><b>EMAIL</b>info@vocaterrana.com</div>
    </div>
    <div class="contact-row">
      <svg width="18" height="18" viewBox="0 0 24 24"><path d="M6 2l4 5-2 2a12 12 0 007 7l2-2 5 4-2 4C10 22 2 14 2 4z" fill="#fff"/></svg>
      <div><b>CALL US</b>014.552.3970</div>
    </div>
    <p class="follow">Follow Us:</p>
    <div class="socials"><span style="background:#3b5998"></span><span style="background:#0e76a8"></span><span style="background:#1da1f2"></span><span style="background:#dd4b39"></span></div>
  </div>
  <div class="inquiry">
    <h3 class="footer-heading">QUICK INQUIRY</h3>
    <div class="form-grid">
      <div class="field">Name</div>
      <div class="field">Email</div>
      <div class="field">Phone</div>
      <div class="field">User Type <svg width="10" height="6" viewBox="0 0 10 6"><path d="M1 1l4 4 4-4" fill="none" stroke="#fff" stroke-width="1.5"/></svg></div>
      <div class="field full">Upload Portfolio <span class="browse">Browse</span></div>
      <div class="field full message">Message</div>
    </div>
    <a class="submit" href="#">SUBMIT</a>
  </div>
  <p class="copyright">Copyright © 2016 VocaTerrana. All Rights Reserved.</p>
</footer>

</body>
</html>
```